Create a memorable Stationary for Security Software Company

Velbrantix is the worldwide leader in securing the Internet. Making Internet communications and critical data secure, reliable and available everywhere has been and continues to be our ongoing vision. We are committed to staying focused on real customer needs and to developing new and innovative security solutions that redefine the security landscape.

Industry/Entity Type

Internet

Font styles to use
Serif
Sans Serif
Script

Colors
0792cd
33a6d7
85cae6

```html
<!DOCTYPE html>
<html lang="en">
<head>
<meta charset="utf-8">
<title>Velbrantix Business Card</title>
<link href="https://fonts.googleapis.com/css2?family=Open+Sans:wght@400;600;700&display=swap" rel="stylesheet">
<style>
  :root {
    --brand-blue: #0792cd;
    --brand-mid: #33a6d7;
    --brand-light: #85cae6;
    --ink: #3a3a3a;
    --paper: #ffffff;
    --backdrop: #e9ecef;
  }
  * { box-sizing: border-box; margin: 0; padding: 0; }
  html, body {
    width: 1200px; height: 1120px; overflow: hidden;
    background: var(--backdrop);
    font-family: "Open Sans", sans-serif;
  }
  .sheet {
    width: 1200px; height: 1120px;
    display: flex; flex-direction: column; align-items: center;
    justify-content: center; gap: 60px;
  }
  .card {
    width: 840px; height: 480px;
    background: var(--paper);
    box-shadow: 0 6px 20px rgba(0,0,0,0.12);
    position: relative;
    overflow: hidden;
  }
  .wordmark {
    display: flex; align-items: center; gap: 14px;
    color: var(--brand-mid);
    font-weight: 700; font-size: 46px; letter-spacing: 0.5px;
  }
  .wordmark-dot {
    width: 34px; height: 34px; border-radius: 50%;
    background: var(--brand-mid);
  }
  /* front */
  .card-front {
    display: flex; flex-direction: column; align-items: center; justify-content: center;
  }
  .card-front .wordmark { margin-top: 20px; }
  .front-url {
    margin-top: 110px;
    color: var(--ink); font-size: 22px; letter-spacing: 3px;
  }
  /* back */
  .card-back { display: flex; }
  .back-logo {
    width: 420px; display: flex; align-items: center; justify-content: center;
  }
  .back-logo .wordmark { font-size: 40px; }
  .divider-stripe { width: 10px; background: var(--brand-blue); }
  .divider-gap { width: 8px; }
  .contact-panel {
    flex: 1; background: var(--brand-blue); color: var(--paper);
    padding: 84px 0 0 48px;
  }
  .contact-name { font-size: 22px; font-weight: 700; }
  .contact-title { font-size: 18px; margin-top: 4px; }
  .contact-list { list-style: none; margin-top: 36px; }
  .contact-list li {
    display: flex; align-items: center; gap: 10px;
    font-size: 17px; line-height: 1.55;
  }
  .contact-list li.address { margin-top: 18px; align-items: flex-start; line-height: 1.35; }
  .icon { width: 16px; height: 16px; flex: none; fill: var(--paper); }
  .address .icon { margin-top: 3px; }
</style>
</head>
<body>
<main class="sheet">
  <section class="card card-front">
    <div class="wordmark"><span class="wordmark-dot"></span>Velbrantix</div>
    <p class="front-url">www.velbrantix.com</p>
  </section>

  <section class="card card-back">
    <div class="back-logo">
      <div class="wordmark"><span class="wordmark-dot"></span>Velbrantix</div>
    </div>
    <div class="divider-stripe"></div>
    <div class="divider-gap"></div>
    <div class="contact-panel">
      <p class="contact-name">Your Name</p>
      <p class="contact-title">Title</p>
      <ul class="contact-list">
        <li>
          <svg class="icon" viewBox="0 0 16 16"><circle cx="8" cy="8" r="7.5" fill="none" stroke="#fff" stroke-width="1.3"/><path d="M5 4.5l1.6-.4 1 2-1 .8c.4 1 1.2 1.8 2.2 2.2l.8-1 2 1-.4 1.6c-3.2.2-6.4-3-6.2-6.2z"/></svg>
          012-345-6789
        </li>
        <li>
          <svg class="icon" viewBox="0 0 16 16"><rect x="4" y="1" width="8" height="14" rx="1.5"/><rect x="5.5" y="3" width="5" height="6" fill="#0792cd"/></svg>
          012-345-6789
        </li>
        <li>
          <svg class="icon" viewBox="0 0 16 16"><rect x="1" y="3.5" width="14" height="9" rx="1"/><path d="M1.5 4l6.5 5 6.5-5" fill="none" stroke="#0792cd" stroke-width="1.3"/></svg>
          info@velbrantix.com
        </li>
        <li>
          <svg class="icon" viewBox="0 0 16 16" fill="none" stroke="#fff" stroke-width="1.2"><circle cx="8" cy="8" r="6.5"/><ellipse cx="8" cy="8" rx="2.8" ry="6.5"/><path d="M1.5 8h13M2.5 4.8h11M2.5 11.2h11"/></svg>
          www.velbrantix.com
        </li>
        <li class="address">
          <svg class="icon" viewBox="0 0 16 16"><path d="M8 0.8a5.5 5.5 0 0 0-5.5 5.5C2.5 10.5 8 15.5 8 15.5s5.5-5 5.5-9.2A5.5 5.5 0 0 0 8 0.8z"/><circle cx="8" cy="6.3" r="2" fill="#0792cd"/></svg>
          <span>Street Name, City Name<br>Zipcode-012345</span>
        </li>
      </ul>
    </div>
  </section>
</main>
</body>
</html>
```